Tandem Hearth Works Pty Ltd

We need business cards for a company based in Perth, we install, service and maintain fire equipment.
On the front we want a great design with our logo and a small spot for our full company name, general company email address and office number. On the back we need space for our name, title, mobile number and email address on the back.

Target Market(s)

Facility managers and commercial/industrial building owners/occupiers.

Contact Information for Business Card

Font styles to use
Sans Serif

Requirements
Must have
• Please only submit 5 of your best samples.
Darker tones are preferred.
Nice to have
• We want to use, black, red and grey. Keep it modern and clean.
I've attached the company logo and a sample of a boarder we use on our emergency plans.
Should not have
• No preference. Let the designer choose.

```html
<!DOCTYPE html>
<html lang="en">
<head>
<meta charset="utf-8">
<title>Tandem Hearth Works – Business Cards</title>
<link href="https://fonts.googleapis.com/css2?family=Arimo:wght@400;700&display=swap" rel="stylesheet">
<style>
  :root {
    --backdrop: #0e0e0f;
    --card: #232325;
    --card-back: #262628;
    --red: #e51b24;
    --grey-text: #c9c9cb;
    --grey-soft: #a9a9ac;
    --emboss: #3a3a3d;
  }
  * { margin: 0; padding: 0; box-sizing: border-box; }
  html, body {
    width: 1200px; height: 820px; overflow: hidden;
    background: radial-gradient(ellipse at 50% 40%, #1b1b1d 0%, var(--backdrop) 75%);
    font-family: "Arimo", Arial, sans-serif;
  }
  .stage {
    position: relative; width: 1200px; height: 820px;
    display: flex; align-items: center; justify-content: center; gap: 60px;
  }
  .card {
    position: relative; width: 525px; height: 300px;
    background: var(--card);
    border-bottom: 3px solid var(--red);
    border-left: 2px solid var(--red);
    box-shadow: 0 20px 40px rgba(0,0,0,.6);
  }
  /* Contact side */
  .wordmark {
    position: absolute; left: 40px; top: 42px;
    font-weight: 700; font-size: 30px; line-height: 1.1;
    color: var(--red); display: flex; align-items: center; gap: 10px;
  }
  .wordmark .mark-square { width: 16px; height: 16px; background: var(--red); }
  .person { position: absolute; left: 40px; top: 176px; }
  .person-name { color: var(--red); font-weight: 700; font-size: 17px; text-transform: uppercase; }
  .person-title { color: var(--grey-text); font-size: 14px; margin-top: 2px; }
  .contact-list { list-style: none; margin-top: 16px; }
  .contact-list li {
    display: flex; align-items: center; gap: 10px;
    color: var(--grey-text); font-size: 14px; line-height: 22px;
  }
  .contact-list svg { width: 14px; height: 14px; flex: none; }
  .company { position: absolute; left: 300px; top: 100px; }
  .company-name {
    color: var(--red); font-weight: 700; font-size: 16px; line-height: 1.15;
    text-transform: uppercase;
  }
  .company-phone { color: var(--grey-text); font-weight: 700; font-size: 21px; margin-top: 8px; }
  .company .contact-list { margin-top: 6px; }
  .company .contact-list li { font-size: 13px; line-height: 19px; }
  /* Logo side */
  .card-back {
    background: var(--card-back);
    border-bottom: 5px solid var(--red);
    border-left: none;
    display: flex; align-items: center; justify-content: center;
  }
  .card-back .wordmark-emboss {
    font-weight: 700; font-size: 34px; color: var(--emboss);
    display: flex; align-items: center; gap: 12px;
  }
  .card-back .mark-square { width: 18px; height: 18px; background: var(--emboss); }
</style>
</head>
<body>
<main class="stage">
  <section class="card card-front" aria-label="Contact side of business card">
    <div class="wordmark"><span class="mark-square"></span>Tandem Hearth Works</div>

    <div class="person">
      <p class="person-name">Marcus Ellery</p>
      <p class="person-title">Managing Director</p>
      <ul class="contact-list">
        <li>
          <svg viewBox="0 0 14 14" aria-hidden="true"><rect x="3" y="1" width="8" height="12" rx="1.5" fill="none" stroke="var(--red)" stroke-width="1.4"/><circle cx="7" cy="11" r=".8" fill="var(--red)"/></svg>
          804.3361.2748
        </li>
        <li>
          <svg viewBox="0 0 14 14" aria-hidden="true"><rect x="1" y="3" width="12" height="8" fill="var(--red)"/><path d="M1 3 L7 8 L13 3" fill="none" stroke="var(--card)" stroke-width="1"/></svg>
          marcus@tandemhearth.com
        </li>
      </ul>
    </div>

    <div class="company">
      <p class="company-name">Tandem Hearth<br>Works Pty Ltd</p>
      <p class="company-phone">804.5512.0937</p>
      <ul class="contact-list">
        <li>
          <svg viewBox="0 0 14 14" aria-hidden="true"><rect x="1" y="3" width="12" height="8" fill="var(--red)"/><path d="M1 3 L7 8 L13 3" fill="none" stroke="var(--card)" stroke-width="1"/></svg>
          info@tandemhearth.com
        </li>
        <li>
          <svg viewBox="0 0 14 14" aria-hidden="true"><circle cx="7" cy="7" r="6" fill="var(--red)"/><path d="M1 7 H13 M7 1 V13 M7 1 C3.5 4 3.5 10 7 13 M7 1 C10.5 4 10.5 10 7 13" fill="none" stroke="var(--card)" stroke-width=".8"/></svg>
          www.tandemhearth.com
        </li>
      </ul>
    </div>
  </section>

  <section class="card card-back" aria-label="Logo side of business card">
    <div class="wordmark-emboss"><span class="mark-square"></span>Tandem Hearth Works</div>
  </section>
</main>
</body>
</html>
```